Fern Lattice Table & Chair Rentals

We need a business card for a table and chair rental company. We rent tables and chairs for weddings, funerals, business events and parties. We want something that looks clean and elegant while not being too busy. We would like colors in the green and blue hues and avoiding anything orange. We want to make sure the font is large enough to be seen easily.

Target Market(s)

Wedding & Event Rentals

Industry/Entity Type

Events

Contact Information for Business Card

Fern Lattice, sales@fernlatticerentals.com, fernlatticerentals.com, 360-555-0182

Requirements
Must have
• Easy to read font
Should not have
• Orange anywhere in the design

```html
<!DOCTYPE html>
<html lang="en">
<head>
<meta charset="utf-8">
<title>Fern Lattice – Business Card</title>
<link href="https://fonts.googleapis.com/css2?family=Open+Sans:wght@400;600&display=swap" rel="stylesheet">
<style>
  :root {
    --backdrop: #3a3a3c;
    --card-green: #4f6b0c;
    --card-green-light: #6f8e1e;
    --card-green-dark: #3c5408;
    --ink: #f4f4ec;
    --divider: rgba(244, 244, 236, 0.85);
  }
  * { margin: 0; padding: 0; box-sizing: border-box; }
  html, body {
    width: 1200px;
    height: 852px;
    overflow: hidden;
    background: var(--backdrop);
    font-family: "Open Sans", Arial, sans-serif;
    color: var(--ink);
  }
  .canvas {
    position: relative;
    width: 1200px;
    height: 852px;
  }
  .card {
    position: absolute;
    width: 525px;
    height: 300px;
    border-radius: 22px;
    overflow: hidden;
    box-shadow: 0 10px 24px rgba(0, 0, 0, 0.45);
  }
  .card--front { left: 70px; top: 110px; }
  .card--back { left: 605px; top: 440px; }
  .card__photo {
    position: absolute;
    inset: 0;
    background:
      radial-gradient(circle at 22% 55%, var(--card-green-light) 0%, transparent 35%),
      radial-gradient(circle at 65% 60%, rgba(150, 180, 70, 0.45) 0%, transparent 30%),
      linear-gradient(120deg, var(--card-green-dark) 0%, var(--card-green) 50%, var(--card-green-light) 100%);
  }
  .front__brand {
    position: absolute;
    left: 70px;
    top: 92px;
  }
  .brand-name {
    font-weight: 400;
    font-size: 56px;
    line-height: 1;
    letter-spacing: 0.5px;
  }
  .front__tagline {
    margin-top: 16px;
    font-size: 24px;
    letter-spacing: 0.5px;
  }
  .back__brand {
    position: absolute;
    left: 36px;
    bottom: 48px;
  }
  .back__brand .brand-name { font-size: 38px; }
  .back__divider {
    position: absolute;
    left: 292px;
    top: 118px;
    width: 2px;
    height: 110px;
    background: var(--divider);
  }
  .contact-list {
    position: absolute;
    left: 312px;
    top: 108px;
    list-style: none;
    font-size: 13.5px;
    line-height: 1;
  }
  .contact-list li {
    display: flex;
    align-items: center;
    gap: 8px;
    margin-bottom: 9px;
  }
  .contact-icon { width: 13px; height: 13px; flex: none; }
</style>
</head>
<body>
<main class="canvas">
  <section class="card card--front">
    <div class="card__photo" role="img" aria-label="Soft-focus photo of a hanging floral ball at an event, tinted green"></div>
    <div class="front__brand">
      <div class="brand-name">Fern Lattice</div>
      <div class="front__tagline">Table and Chair Rentals</div>
    </div>
  </section>

  <section class="card card--back">
    <div class="card__photo" role="img" aria-label="Soft-focus photo of a hanging floral ball at an event, tinted green"></div>
    <div class="back__brand">
      <div class="brand-name">Fern Lattice</div>
    </div>
    <div class="back__divider"></div>
    <ul class="contact-list">
      <li>
        <svg class="contact-icon" viewBox="0 0 16 16" aria-hidden="true"><path fill="#f4f4ec" d="M3 1l3 3-1.5 2a9 9 0 0 0 5.5 5.5L12 10l3 3-2 2C7 15 1 9 1 3z"/></svg>
        <span>360-555-0182</span>
      </li>
      <li>
        <svg class="contact-icon" viewBox="0 0 16 16" aria-hidden="true"><rect x="1" y="3" width="14" height="10" rx="1" fill="#f4f4ec"/><path d="M1.5 3.5L8 9l6.5-5.5" stroke="#4f6b0c" stroke-width="1.4" fill="none"/></svg>
        <span>sales@fernlatticerentals.com</span>
      </li>
      <li>
        <svg class="contact-icon" viewBox="0 0 16 16" aria-hidden="true"><circle cx="8" cy="8" r="7" fill="#f4f4ec"/><path d="M1 8h14M8 1c-3 3.5-3 10.5 0 14M8 1c3 3.5 3 10.5 0 14" stroke="#4f6b0c" stroke-width="1.1" fill="none"/></svg>
        <span>www.fernlatticerentals.com</span>
      </li>
    </ul>
  </section>
</main>
</body>
</html>
```